Moravel Aesthetic Doctor

I require an elegant, luxurious looking business card for my aesthetic business. I am a doctor and that will set me aside from competitors. I am planning to provide home and spa based treatments to clients with high expectations. I have attached my logo.

```html
<!DOCTYPE html>
<html lang="en">
<head>
<meta charset="utf-8">
<title>Moravel Aesthetic Doctor – Business Card</title>
<link href="https://fonts.googleapis.com/css2?family=Roboto:wght@300;400;500&display=swap" rel="stylesheet">
<style>
  :root {
    --page-bg: #e9ebee;
    --brand-blue: #1f5ea8;
    --brand-blue-dark: #1a4f8f;
    --wave-light: #a9d8f2;
    --wave-mid: #5fb3e4;
    --wave-deep: #3f78b8;
    --sky-text: #6cc0ea;
    --ink-grey: #8f9499;
    --logo-grey: #8d9297;
    --card-white: #ffffff;
  }
  * { margin: 0; padding: 0; box-sizing: border-box; }
  html, body { width: 1200px; height: 1200px; overflow: hidden; }
  body {
    background: var(--page-bg);
    font-family: "Roboto", Arial, sans-serif;
    position: relative;
  }
  .card {
    position: absolute;
    left: 150px;
    width: 900px;
    height: 514px;
    box-shadow: 0 6px 18px rgba(0,0,0,0.12);
  }
  /* Back side */
  .card-back {
    top: 48px;
    background: var(--brand-blue);
    overflow: hidden;
  }
  .card-back .portrait-art {
    position: absolute;
    left: 0; top: 0;
    width: 560px; height: 514px;
    background: linear-gradient(100deg, var(--wave-deep) 0%, var(--wave-mid) 45%, var(--wave-light) 80%, var(--brand-blue) 100%);
    opacity: 0.9;
  }
  .card-back .brand {
    position: absolute;
    right: 60px; top: 96px;
    text-align: right;
    color: #ffffff;
    font-weight: 300;
  }
  .brand .brand-name { font-size: 58px; letter-spacing: 4px; line-height: 1; }
  .brand .brand-sub { font-size: 20px; letter-spacing: 4px; margin-top: 6px; }
  .services {
    position: absolute;
    right: 60px; bottom: 60px;
    list-style: none;
    text-align: right;
    color: #ffffff;
    font-size: 23px;
    font-weight: 400;
    line-height: 1.45;
    letter-spacing: 0.5px;
  }
  /* Front side */
  .card-front {
    top: 630px;
    background: var(--card-white);
  }
  .logo-lockup {
    position: absolute;
    left: 0; right: 0; top: 70px;
    display: flex;
    justify-content: center;
    align-items: center;
    gap: 26px;
  }
  .logo-lockup .logo-dot {
    width: 110px; height: 110px;
    border-radius: 50%;
    background: var(--sky-text);
  }
  .logo-lockup .logo-text { color: var(--logo-grey); font-weight: 300; }
  .logo-text .brand-name { font-size: 72px; letter-spacing: 6px; line-height: 1; }
  .logo-text .brand-sub { font-size: 26px; letter-spacing: 5px; margin-top: 6px; }
  .doctor {
    position: absolute;
    left: 0; right: 0; top: 250px;
    text-align: center;
  }
  .doctor .doctor-name {
    color: var(--sky-text);
    font-size: 34px;
    font-weight: 500;
  }
  .doctor .doctor-name small { font-size: 18px; margin-left: 6px; }
  .doctor .doctor-title {
    color: var(--ink-grey);
    font-size: 24px;
    font-weight: 300;
    margin-top: 4px;
  }
  .social {
    position: absolute;
    left: 0; right: 0; top: 368px;
    display: flex; justify-content: center; gap: 22px;
  }
  .social span {
    width: 32px; height: 32px; border-radius: 50%;
    background: var(--sky-text);
  }
  .contact-row {
    position: absolute;
    left: 0; right: 0; bottom: 56px;
    display: flex; justify-content: center; gap: 40px;
    color: var(--ink-grey);
    font-size: 24px; font-weight: 300;
  }
  .contact-row .item { display: flex; align-items: center; gap: 12px; }
  .contact-row svg { width: 22px; height: 22px; stroke: var(--sky-text); fill: none; stroke-width: 1.8; }
  .contact-row .accent { color: var(--sky-text); }
</style>
</head>
<body>
  <section class="card card-back">
    <div class="portrait-art" role="img" aria-label="Flowing blue wave illustration forming a profile with streaming hair"></div>
    <div class="brand">
      <div class="brand-name">MORAVEL</div>
      <div class="brand-sub">AESTHETIC DOCTOR</div>
    </div>
    <ul class="services">
      <li>Dermal injectables</li>
      <li>Plasma facials</li>
      <li>Microneedling</li>
      <li>Skin boosters</li>
      <li>Excessive sweating</li>
      <li>Home and Spa Based Treatments</li>
    </ul>
  </section>

  <section class="card card-front">
    <div class="logo-lockup">
      <span class="logo-dot"></span>
      <div class="logo-text">
        <div class="brand-name">MORAVEL</div>
        <div class="brand-sub">AESTHETIC DOCTOR</div>
      </div>
    </div>
    <div class="doctor">
      <div class="doctor-name">Dr Elise Varkov,<small>MRCPCH MD</small></div>
      <div class="doctor-title">Australasian Diploma of Aesthetic Medicine</div>
    </div>
    <div class="social"><span></span><span></span></div>
    <div class="contact-row">
      <div class="item">
        <svg viewBox="0 0 24 24"><path d="M5 3h4l2 5-3 2a11 11 0 0 0 6 6l2-3 5 2v4a2 2 0 0 1-2 2A17 17 0 0 1 3 5a2 2 0 0 1 2-2z"/></svg>
        0800 555 014
      </div>
      <div class="item">
        <svg viewBox="0 0 24 24"><rect x="3" y="6" width="18" height="12"/><path d="M3 6l9 7 9-7"/></svg>
        elise@moravel.co.nz
      </div>
      <div class="item">
        <svg viewBox="0 0 24 24"><circle cx="12" cy="12" r="9"/><path d="M3 12h18M12 3c3 3 3 15 0 18M12 3c-3 3-3 15 0 18"/></svg>
        <span>www.<span class="accent">moravel</span>.co.nz</span>
      </div>
    </div>
  </section>
</body>
</html>
```